Business Card Design

Business Card for professional consulting firm working with large financial institutions.

Target Market(s)

Executive buyers

Industry/Entity Type

Banking

Contact Information for Business Card

Mild creativity wanted. Not boring, but do elaborate artwork.

Font styles to use
Serif
Sans Serif

Colors

Designer to choose colors to be used in the design.

Requirements
Must have
• Standard business card features - company name, individual name, telephone, website, email, locations.
Nice to have
• Two colors
Should not have
• too many colors, fancy printing, cartoons.

```html
<!DOCTYPE html>
<html lang="en">
<head>
<meta charset="utf-8">
<title>Northvale Business Card</title>
<link rel="stylesheet" href="https://fonts.googleapis.com/css2?family=Lato:wght@400;700&display=swap">
<style>
  :root {
    --brand-blue: #0b2f8a;
    --card-white: #f4f4f4;
    --swoosh-grey: #c6c6c6;
    --text-grey: #3a3a3a;
    --page-bg: #e6e3de;
    --white: #ffffff;
  }
  * { margin: 0; padding: 0; box-sizing: border-box; }
  html, body {
    width: 1200px;
    height: 900px;
    overflow: hidden;
    background: var(--page-bg);
    font-family: "Lato", Arial, sans-serif;
  }
  .sheet {
    width: 1200px;
    height: 900px;
    display: flex;
    align-items: center;
    justify-content: center;
    gap: 30px;
  }
  .card {
    position: relative;
    width: 560px;
    height: 320px;
    overflow: hidden;
    box-shadow: 0 6px 18px rgba(0,0,0,0.18);
  }
  .card-back {
    background: var(--brand-blue);
    display: flex;
    align-items: center;
    justify-content: center;
  }
  .brand-name {
    display: flex;
    align-items: center;
    gap: 10px;
    font-weight: 400;
    letter-spacing: 0.5px;
  }
  .brand-dot {
    width: 12px;
    height: 12px;
    border-radius: 50%;
  }
  .card-back .brand-name { color: var(--white); font-size: 40px; }
  .card-back .brand-dot { background: var(--white); }

  .card-front { background: var(--card-white); }
  .front-wave {
    position: absolute;
    inset: 0;
  }
  .front-brand {
    position: absolute;
    top: 58px;
    right: 46px;
    color: var(--brand-blue);
    font-size: 32px;
  }
  .front-brand .brand-dot { background: var(--swoosh-grey); }
  .holder {
    position: absolute;
    top: 72px;
    left: 48px;
  }
  .holder-name {
    color: var(--brand-blue);
    font-weight: 700;
    font-size: 19px;
    letter-spacing: 0.4px;
    text-transform: uppercase;
  }
  .holder-title {
    color: var(--text-grey);
    font-size: 14px;
    margin-top: 2px;
  }
  .contacts {
    position: absolute;
    top: 160px;
    left: 82px;
    color: var(--text-grey);
    font-size: 15px;
    line-height: 1.35;
  }
  .contact-line { display: flex; align-items: center; gap: 7px; }
  .contact-line svg { width: 13px; height: 13px; fill: var(--brand-blue); }
  .address { margin-top: 10px; font-size: 16px; }
  .website {
    position: absolute;
    right: 40px;
    top: 218px;
    color: var(--white);
    font-size: 13px;
    letter-spacing: 0.2px;
  }
</style>
</head>
<body>
<main class="sheet">
  <section class="card card-back">
    <div class="brand-name"><span class="brand-dot"></span>northvale</div>
  </section>

  <section class="card card-front">
    <svg class="front-wave" viewBox="0 0 560 320" preserveAspectRatio="none" aria-hidden="true">
      <path d="M0,282 C170,292 380,260 560,142 L560,160 C380,280 170,302 0,300 Z" fill="var(--swoosh-grey)"/>
      <path d="M0,300 C170,302 380,280 560,160 L560,320 L0,320 Z" fill="var(--brand-blue)"/>
    </svg>

    <div class="brand-name front-brand"><span class="brand-dot"></span>northvale</div>

    <div class="holder">
      <div class="holder-name">Daniel Hartley</div>
      <div class="holder-title">Managing Director</div>
    </div>

    <div class="contacts">
      <div class="contact-line">
        <svg viewBox="0 0 24 24" aria-hidden="true"><path d="M6.6 10.8a15 15 0 0 0 6.6 6.6l2.2-2.2a1 1 0 0 1 1-.25 11.4 11.4 0 0 0 3.6.57 1 1 0 0 1 1 1V20a1 1 0 0 1-1 1A17 17 0 0 1 3 4a1 1 0 0 1 1-1h3.5a1 1 0 0 1 1 1c0 1.25.2 2.45.57 3.6a1 1 0 0 1-.25 1z"/></svg>
        020-555 014 732
      </div>
      <div class="contact-line">
        <svg viewBox="0 0 24 24" aria-hidden="true"><path d="M2 5h20v14H2z M2 5l10 8 10-8" /></svg>
        hello@northvale.com
      </div>
      <div class="address">48 Harbour Street<br>Eastbridge, 40219</div>
    </div>

    <div class="website">www.northvale.com</div>
  </section>
</main>
</body>
</html>
```